Business Card for a Dental Office

The design should communicate integrity, quality and reliability. We also want the card look elegant, simple, but still stand out, different from the traditional-dental-office business card.

Industry/Entity Type

Business

```html
<!DOCTYPE html>
<html lang="en">
<head>
<meta charset="UTF-8">
<title>Harlow Dental Studio – Business Card</title>
<link href="https://fonts.googleapis.com/css2?family=Oswald:wght@600&family=Open+Sans:wght@400;600&display=swap" rel="stylesheet">
<style>
  :root {
    --ink: #0d0d0d;
    --paper: #ffffff;
    --accent: #e6d21f;
    --gold: #bfa330;
    --text-grey: #4a4a4a;
    --backdrop: #e9e6e1;
  }
  * { box-sizing: border-box; margin: 0; padding: 0; }
  html, body { width: 1200px; height: 843px; overflow: hidden; }
  body {
    background: var(--backdrop);
    font-family: "Open Sans", Arial, sans-serif;
    position: relative;
  }
  .card {
    position: absolute;
    left: 300px;
    width: 600px;
    height: 343px;
    overflow: hidden;
    box-shadow: 0 10px 28px rgba(0,0,0,.25);
  }
  .card-back { top: 40px; background: var(--ink); }
  .card-front { top: 420px; background: var(--ink); }
  .card-shapes { position: absolute; inset: 0; width: 100%; height: 100%; }

  /* back side */
  .back-mark {
    position: absolute; left: 60px; top: 92px;
    width: 160px; height: 160px; background: var(--accent);
  }
  .back-brand {
    position: absolute; left: 250px; top: 135px;
    color: var(--accent);
  }
  .back-brand .brand-name {
    font-family: "Oswald", "Arial Narrow", sans-serif;
    font-weight: 600; font-size: 28px; letter-spacing: .5px;
    text-transform: uppercase; line-height: 1;
  }
  .back-brand .tagline { font-size: 11px; font-weight: 600; letter-spacing: .6px; text-transform: uppercase; margin-top: 6px; }
  .back-brand .web { font-size: 16px; letter-spacing: 1.5px; margin-top: 4px; }

  /* front side */
  .holder {
    position: absolute; right: 30px; top: 34px;
    color: var(--paper); text-align: right;
  }
  .holder .name { font-weight: 600; font-size: 19px; letter-spacing: .5px; line-height: 24px; }
  .holder .role { font-size: 13px; line-height: 18px; }

  .front-brand {
    position: absolute; left: 100px; top: 104px;
    display: flex; align-items: center; gap: 12px;
  }
  .front-brand .mark { width: 44px; height: 44px; background: var(--ink); flex: none; }
  .front-brand .brand-name {
    font-family: "Oswald", "Arial Narrow", sans-serif;
    font-weight: 600; font-size: 28px; color: var(--ink);
    text-transform: uppercase; line-height: 1;
  }
  .front-brand .tagline {
    font-size: 10px; font-weight: 600; color: var(--gold);
    letter-spacing: .5px; text-transform: uppercase; margin-top: 4px;
  }

  .contact-list {
    position: absolute; left: 36px; top: 172px;
    list-style: none; font-size: 14px; color: var(--text-grey); line-height: 23px;
  }
  .contact-list li { display: flex; align-items: center; gap: 9px; }
  .contact-list svg { width: 13px; height: 13px; fill: var(--ink); flex: none; }

  .address {
    position: absolute; right: 34px; bottom: 24px;
    text-align: right; font-size: 15px; color: var(--text-grey); line-height: 21px;
    font-style: normal;
  }
</style>
</head>
<body>

  <section class="card card-back" aria-label="Card back">
    <div class="back-mark"></div>
    <div class="back-brand">
      <div class="brand-name">Harlow Dental Studio</div>
      <div class="tagline">Your smile is your gift to others</div>
      <div class="web">www.harlowdental.com</div>
    </div>
  </section>

  <section class="card card-front" aria-label="Card front">
    <svg class="card-shapes" viewBox="0 0 600 343" preserveAspectRatio="none" aria-hidden="true">
      <polygon points="0,56 380,0 600,250 600,268 380,18 0,70" fill="var(--accent)"/>
      <polygon points="0,70 380,18 600,268 600,343 0,343" fill="var(--paper)"/>
    </svg>

    <div class="holder">
      <div class="name">Daniel Reyes</div>
      <div class="role">CEO/Founder</div>
    </div>

    <div class="front-brand">
      <div class="mark"></div>
      <div>
        <div class="brand-name">Harlow Dental Studio</div>
        <div class="tagline">Your smile is your gift to others</div>
      </div>
    </div>

    <ul class="contact-list">
      <li>
        <svg viewBox="0 0 24 24"><path d="M6.6 10.8a15.1 15.1 0 0 0 6.6 6.6l2.2-2.2a1 1 0 0 1 1-.25 11.4 11.4 0 0 0 3.6.57 1 1 0 0 1 1 1V20a1 1 0 0 1-1 1A17 17 0 0 1 3 4a1 1 0 0 1 1-1h3.5a1 1 0 0 1 1 1c0 1.25.2 2.45.57 3.57a1 1 0 0 1-.25 1z"/></svg>
        512 308 4471
      </li>
      <li>
        <svg viewBox="0 0 24 24"><path d="M3 3h18v18H3zM5 5v14h14V5z"/></svg>
        512 774 2096
      </li>
      <li>
        <svg viewBox="0 0 24 24"><path d="M2 5h20v14H2zm2 2v.5l8 5 8-5V7zm0 2.8V17h16V9.8l-8 5z"/></svg>
        hello@harlowdental.com
      </li>
    </ul>

    <address class="address">
      2140 Alder Creek Road<br>
      Fairbanks, Alaska 99701<br>
      www.harlowdental.com
    </address>
  </section>

</body>
</html>
```